Pellmora Business Cards

Create new business cards with the details below.

Stuart Kovan
Director

MB: +61 427 315 964
PH: 1300 647 519
Email: stuart.kovan@pellmora.com.au
Address: 27D Halden Parade, Brookvale VIC 3174 Australia
Website: www.pellmora.com.au

Target Market(s)

Other business

Industry/Entity Type

Business

Requirements
Must have
• must be clean looking

```html
<!DOCTYPE html>
<html lang="en">
<head>
<meta charset="UTF-8">
<title>Pellmora Business Cards</title>
<link href="https://fonts.googleapis.com/css2?family=Exo+2:wght@400;600;700&display=swap" rel="stylesheet">
<style>
  :root {
    --backdrop: #e4e4e4;
    --card: #ffffff;
    --lime: #9bc93a;
    --ink: #2b2b2b;
    --soft-ink: #555555;
    --icon-blue: #2b8fd6;
  }
  * { margin: 0; padding: 0; box-sizing: border-box; }
  html, body { width: 1200px; height: 894px; overflow: hidden; }
  body {
    background: var(--backdrop);
    font-family: "Exo 2", sans-serif;
    color: var(--ink);
    position: relative;
  }
  .card {
    position: absolute;
    left: 250px;
    width: 700px;
    height: 400px;
    background: var(--card);
    box-shadow: 0 4px 14px rgba(0,0,0,0.12);
    overflow: hidden;
  }
  .card--back { top: 36px; }
  .card--front { top: 458px; }

  .brand {
    display: flex;
    align-items: center;
    gap: 12px;
  }
  .brand__square {
    width: 30px; height: 30px;
    background: var(--lime);
  }
  .brand__name {
    font-weight: 700;
    color: var(--ink);
    letter-spacing: 1px;
    text-transform: uppercase;
    line-height: 1;
  }
  .card--back .brand {
    position: absolute;
    left: 50%; top: 50%;
    transform: translate(-50%, -50%);
  }
  .card--back .brand__name { font-size: 56px; }
  .card--back .brand__square { width: 44px; height: 44px; }

  .card--front .brand {
    position: absolute;
    left: 56px; top: 44px;
  }
  .card--front .brand__name { font-size: 50px; }
  .card--front .brand__square { width: 40px; height: 40px; }

  .person {
    position: absolute;
    left: 60px; top: 126px;
    text-transform: uppercase;
  }
  .person__name {
    font-size: 24px;
    font-weight: 600;
    letter-spacing: 1px;
  }
  .person__title {
    font-size: 14px;
    color: var(--soft-ink);
    letter-spacing: 1.5px;
    margin-top: 2px;
  }

  .contact {
    position: absolute;
    list-style: none;
    font-size: 15px;
    color: var(--ink);
  }
  .contact li {
    display: flex;
    align-items: flex-start;
    gap: 10px;
    margin-bottom: 8px;
    line-height: 1.3;
  }
  .contact svg { flex: none; width: 16px; height: 16px; margin-top: 2px; }
  .contact--place { left: 60px; top: 200px; width: 280px; }
  .contact--reach { left: 400px; top: 248px; }

  .band {
    position: absolute;
    height: 12px;
  }
  .band--lime { background: var(--lime); left: 0; width: 330px; top: 250px; }
  .band--ink { background: var(--ink); left: 330px; width: 320px; top: 364px; height: 14px; }
</style>
</head>
<body>
  <section class="card card--back" aria-label="Card back">
    <div class="brand">
      <span class="brand__square"></span>
      <span class="brand__name">Pellmora</span>
    </div>
  </section>

  <section class="card card--front" aria-label="Card front">
    <div class="brand">
      <span class="brand__square"></span>
      <span class="brand__name">Pellmora</span>
    </div>

    <div class="person">
      <p class="person__name">Stuart Kovan</p>
      <p class="person__title">Director</p>
    </div>

    <ul class="contact contact--place">
      <li>
        <svg viewBox="0 0 16 16" aria-hidden="true"><path d="M8 1a5 5 0 0 0-5 5c0 4 5 9 5 9s5-5 5-9a5 5 0 0 0-5-5zm0 7a2 2 0 1 1 0-4 2 2 0 0 1 0 4z" fill="var(--icon-blue)"/></svg>
        <span>27D Halden Parade,<br>Brookvale VIC 3174</span>
      </li>
      <li style="margin-top:26px">
        <svg viewBox="0 0 16 16" aria-hidden="true"><circle cx="8" cy="8" r="6.5" fill="none" stroke="var(--icon-blue)" stroke-width="1.5"/><path d="M1.5 8h13M8 1.5c-3 3.5-3 9.5 0 13M8 1.5c3 3.5 3 9.5 0 13" fill="none" stroke="var(--icon-blue)" stroke-width="1.2"/></svg>
        <span>www.pellmora.com.au</span>
      </li>
    </ul>

    <div class="band band--lime"></div>

    <ul class="contact contact--reach">
      <li>
        <svg viewBox="0 0 16 16" aria-hidden="true"><path d="M4 1.5l2.5 3-1.5 1.5c.8 2 2.5 3.7 4.5 4.5l1.5-1.5 3 2.5-1.5 2.5C7 14 2 9 1.5 3z" fill="var(--icon-blue)"/></svg>
        <span>+61 427 315 964</span>
      </li>
      <li>
        <svg viewBox="0 0 16 16" aria-hidden="true"><rect x="4" y="1" width="8" height="14" rx="1.5" fill="none" stroke="var(--icon-blue)" stroke-width="1.5"/><circle cx="8" cy="12.5" r="0.9" fill="var(--icon-blue)"/></svg>
        <span>1300 647 519</span>
      </li>
      <li>
        <svg viewBox="0 0 16 16" aria-hidden="true"><rect x="1" y="3" width="14" height="10" rx="1" fill="var(--icon-blue)"/><path d="M1.5 3.5L8 9l6.5-5.5" fill="none" stroke="#fff" stroke-width="1.2"/></svg>
        <span>stuart.kovan@pellmora.com.au</span>
      </li>
    </ul>

    <div class="band band--ink"></div>
  </section>
</body>
</html>
```